Redesign of Form/Document Navigation Page

I need a redesign of our document and navigation bar on the left. We want the same navigation bar layout/setup but want the buttons and typography to be simple and matching all over. The form needs to be aesthetically pleasing and fit within the page.

1st attachment is our Direct Deposit and the second is the form continued.

```html
<!DOCTYPE html>
<html lang="en">
<head>
<meta charset="utf-8">
<title>Employee Direct Deposit Enrollment Form</title>
<link href="https://fonts.googleapis.com/css2?family=Open+Sans:wght@400;600&display=swap" rel="stylesheet">
<style>
:root{
  --brand-blue:#2b63ad;
  --brand-blue-dark:#1f4a8a;
  --title-blue:#2d5fa3;
  --gold:#f0b52b;
  --page-grey:#f2f2f2;
  --line:#d3d3d3;
  --text:#555;
  --text-soft:#7a7a7a;
  --ink:#333;
  --white:#fff;
}
*{box-sizing:border-box;margin:0;padding:0}
html,body{width:1200px;height:1004px;overflow:hidden}
body{position:relative;background:var(--page-grey);font-family:"Open Sans",Arial,sans-serif;color:var(--text)}
.abs{position:absolute}

/* header */
.site-header{left:0;top:0;width:1200px;height:91px;background:var(--white);border-bottom:2px solid #dcdcdc}
.brand{left:130px;top:34px;display:flex;align-items:center;gap:10px}
.brand-dot{width:24px;height:24px;border-radius:50%;background:var(--brand-blue)}
.brand-name{font-weight:600;font-size:19px;line-height:24px;color:var(--title-blue);white-space:nowrap}
.top-nav{top:44px;display:flex;align-items:center;gap:7px;font-size:14px;color:var(--ink);letter-spacing:.3px}
.top-nav svg{fill:#a8a8a8}
.nav-home{left:738px}
.nav-help{left:842px}
.user-chip{left:962px;top:35px;width:112px;height:34px;background:#e4e4e4;display:flex;align-items:center;justify-content:center;gap:6px;font-size:13.5px;color:#555}
.user-chip svg{fill:#888}

/* sidebar */
.side-nav{left:136px;top:135px}
.side-item{position:absolute;left:0;width:232px;height:46px}
.side-bar{position:absolute;left:2px;top:3px;width:230px;height:42px;background:linear-gradient(180deg,var(--brand-blue),var(--brand-blue-dark));color:var(--white);font-size:15px;letter-spacing:.1px;line-height:42px;padding-left:56px;white-space:nowrap}
.side-icon{position:absolute;left:0;top:0;width:48px;height:48px;border-radius:50%;background:var(--brand-blue-dark);border:4px solid var(--gold);display:flex;align-items:center;justify-content:center}
.side-icon svg{fill:none;stroke:var(--white);stroke-width:2}

/* form panel */
.form-panel{left:379px;top:137px;width:686px;height:720px;background:var(--white);border:1px solid #cfcfcf}
.form-title{left:408px;top:160px;font-size:21px;color:var(--title-blue);letter-spacing:.3px;font-weight:400}
.body-copy{font-size:12px;line-height:20px;color:var(--text-soft)}
.intro{left:406px;top:202px;width:620px}
.attach-band{left:404px;top:283px;width:639px;height:54px;background:var(--gold);display:flex;align-items:center;padding-left:23px;color:var(--white);font-size:16px;letter-spacing:.2px}
.refresh-btn{position:absolute;left:511px;top:12px;width:97px;height:31px;border-radius:16px;background:linear-gradient(180deg,#3566b0,#1c4586);color:var(--white);font-size:14px;text-align:center;line-height:30px}
.section-title{left:408px;top:356px;font-size:17px;color:var(--title-blue);font-weight:400}
.account-note{left:405px;top:382px;width:630px;font-size:12.5px}
.account-link{left:405px;top:423px;font-size:13px;color:var(--title-blue)}
.notify{left:404px;top:469px;font-size:14.5px;color:var(--title-blue);letter-spacing:.1px}
.radio-row{display:flex;align-items:center;font-size:13px;color:var(--text-soft)}
.radio{width:17px;height:17px;border-radius:50%;border:1px solid #c4c4c4;margin-right:6px;flex:none}
.enroll-options{left:404px;top:500px;gap:12px}
.enroll-options span{display:flex;align-items:center}
.field{height:36px;border:1px solid var(--line);background:var(--white);font-size:12.5px;color:#8a8a8a;padding-left:13px;line-height:34px}
.amount-label{left:629px;top:657px;font-size:13px;color:var(--text-soft)}
.amount-field{color:var(--ink)}
.important{left:413px;top:723px;font-size:13px;color:var(--ink)}
.terms{left:411px;top:749px;width:620px}

/* footer */
.site-footer{left:0;top:912px;width:1200px;height:92px;background:var(--white);border-top:2px solid #dcdcdc}
.copyright{left:134px;top:943px;font-size:13px;color:#555}
.social{top:937px;width:32px;height:32px;border-radius:50%;border:2px solid var(--brand-blue)}
</style>
</head>
<body>

<header class="site-header abs">
  <div class="brand abs"><span class="brand-dot"></span><span class="brand-name">Summit Watch Security</span></div>
  <nav>
    <a class="top-nav nav-home abs"><svg width="20" height="18" viewBox="0 0 20 18"><path d="M10 1 1 9h3v8h4v-5h4v5h4V9h3z"/></svg>HOME</a>
    <a class="top-nav nav-help abs"><svg width="22" height="18" viewBox="0 0 22 18"><ellipse cx="11" cy="8" rx="10" ry="7"/><path d="M4 12 2 17l6-3z"/></svg>HELP</a>
  </nav>
  <div class="user-chip abs"><svg width="13" height="14" viewBox="0 0 13 14"><circle cx="6.5" cy="4" r="3.5"/><path d="M0 14c0-4 3-6 6.5-6S13 10 13 14z"/></svg>Dana Reyes</div>
</header>

<nav class="side-nav abs">
  <div class="side-item" style="top:0"><div class="side-bar">Direct Deposit</div><div class="side-icon"><svg width="22" height="16" viewBox="0 0 22 16"><rect x="1" y="2" width="20" height="12" rx="1"/><circle cx="11" cy="8" r="3"/></svg></div></div>
  <div class="side-item" style="top:51px"><div class="side-bar">Change W-4</div><div class="side-icon"><svg width="20" height="20" viewBox="0 0 20 20"><path d="M3 7h5V4a2 2 0 0 1 4 0v3h5v10H3z"/></svg></div></div>
  <div class="side-item" style="top:102px"><div class="side-bar">Labour Code</div><div class="side-icon"><svg width="20" height="20" viewBox="0 0 20 20"><circle cx="10" cy="10" r="3"/><circle cx="10" cy="10" r="7" stroke-dasharray="3 2.5" stroke-width="3"/></svg></div></div>
  <div class="side-item" style="top:153px"><div class="side-bar">Personal Information</div><div class="side-icon"><svg width="20" height="20" viewBox="0 0 20 20"><circle cx="10" cy="10" r="8"/><path d="M10 9v6M10 5v1.5"/></svg></div></div>
  <div class="side-item" style="top:204px"><div class="side-bar">Appraisal and Review</div><div class="side-icon"><svg width="20" height="20" viewBox="0 0 20 20"><path d="M3 8h4l8-5v14l-8-5H3zM6 12l1 5"/></svg></div></div>
  <div class="side-item" style="top:255px"><div class="side-bar">Write Up-Slip</div><div class="side-icon"><svg width="20" height="20" viewBox="0 0 20 20"><rect x="3" y="6" width="9" height="12"/><path d="M8 6V2h9v12h-5"/></svg></div></div>
  <div class="side-item" style="top:306px"><div class="side-bar">Employee Performance</div><div class="side-icon"><svg width="20" height="20" viewBox="0 0 20 20"><path d="M2 2v16h16M5 13l4-4 3 3 6-6"/></svg></div></div>
</nav>

<main>
  <section class="form-panel abs"></section>
  <h1 class="form-title abs">Employee Direct Deposit Enrollment Form</h1>
  <p class="body-copy intro abs">Captain &amp; Maritime eleifend libero a tempus libero lectus feugiat felis Morbi diam mauris viverra in gravida eu mattis in ante Morbi eget arcu Morbi porta libero id ullamcorper nonummy nibh ligula pulvinar metus eget consectetuer augue nisi quis lacus Ut ac mi quis lacus mollis aliquam Curabitur</p>

  <div class="attach-band abs">Attach a Voided Check or Bank Deposit from for the Account<span class="refresh-btn">Refresh</span></div>

  <h2 class="section-title abs">Account Information</h2>
  <p class="body-copy account-note abs">The last item must be for the remaining amount owed to you. To distribute to more accounts. Please complete another form.</p>
  <p class="account-link abs">Make sure to indicate what kind of account, along with enrolling or declining</p>
  <p class="notify abs">NOTIFY PAYROLL IMMEDIATELY IF YOU CLOSE OR CHANGE BANK ACCOUNT</p>

  <div class="radio-row enroll-options abs">
    <span><i class="radio"></i>New Enrollement</span>
    <span><i class="radio"></i>Change Enrollment</span>
    <span><i class="radio"></i>Cancel Enrollment</span>
  </div>

  <div class="field abs" style="left:411px;top:555px;width:202px">Bank Name</div>
  <div class="field abs" style="left:625px;top:555px;width:202px">City</div>
  <div class="field abs" style="left:838px;top:555px;width:202px">State</div>
  <div class="field abs" style="left:412px;top:603px;width:202px">Routing Transit</div>
  <div class="field abs" style="left:626px;top:603px;width:202px">Account Number</div>

  <div class="radio-row abs" style="left:411px;top:659px"><i class="radio"></i>Checking</div>
  <div class="radio-row abs" style="left:511px;top:659px"><i class="radio"></i>Savings</div>
  <span class="amount-label abs">Amount Number</span>
  <div class="field amount-field abs" style="left:739px;top:651px;width:89px;height:35px">100 &nbsp;%</div>

  <p class="important abs">IMPORTANT! please read and sign before completing and submitting</p>
  <p class="body-copy terms abs">Captain &amp; Maritime eleifend libero a tempus libero lectus feugiat felis Morbi diam mauris viverra in gravida eu mattis in ante Morbi eget arcu Morbi porta libero id ullamcorper nonummy nibh ligula pulvinar metus eget consectetuer augue nisi quis lacus Ut ac mi quis lacus mollis aliquam Curabitur</p>
</main>

<footer class="site-footer abs"></footer>
<p class="copyright abs">© 2016 Company Name &nbsp;All right reserved &nbsp;Term of Use</p>
<span class="social abs" style="left:929px"></span>
<span class="social abs" style="left:963px"></span>
<span class="social abs" style="left:996px"></span>
<span class="social abs" style="left:1029px"></span>

</body>
</html>
```